Nivel Crest - Powerpoint Templates

We are a consultancy to help builders to optimize their planning in order to save building costs. For that reason we need templates for teasers and presentations where we offer our services, show our team and their capacities and present workflows, organization charts, price lists etc.

```html
<!DOCTYPE html>
<html lang="en">
<head>
<meta charset="utf-8">
<title>Nivel Crest – Presentation Template</title>
<link href="https://fonts.googleapis.com/css2?family=Montserrat:wght@400;500;600;700;800&display=swap" rel="stylesheet">
<style>
:root{
  --gold:#c8902e;--gold-l:#e4b250;--gold-d:#9a6618;--brown:#6e4215;
  --ink:#1f1f23;--dark:#232328;--grey:#7c7c7c;--text:#5f5f5f;--line:#e4e4e4;--paper:#ffffff;
  --photo-site:linear-gradient(150deg,#e8b45a 0%,#b97a2c 35%,#4f4236 70%,#2c3442 100%);
  --photo-sky:linear-gradient(160deg,#b8c9dc 0%,#dfe6ee 45%,#c9a66a 100%);
  --photo-warm:linear-gradient(135deg,#d8c7ac 0%,#c98d3d 50%,#5f5348 100%);
}
*{box-sizing:border-box;margin:0;padding:0}
html,body{width:708px;height:1200px;overflow:hidden;background:var(--paper)}
body{font-family:'Montserrat',sans-serif;color:var(--ink)}
.canvas{position:relative;width:708px;height:1200px;background:#fff}
.defs{position:absolute;width:0;height:0}

.hero{position:absolute;top:14px;left:76px;display:grid;grid-template-columns:repeat(2,auto);gap:14px 16px}
.hero .slide{font-size:9.15px}
.hero .p{font-size:.36em}
.deck{position:absolute;top:352px;left:32px;display:grid;grid-template-columns:repeat(5,118px);gap:16px 13.5px}
.deck .slide{font-size:4px}

.slide{position:relative;width:29.5em;height:16.6em;background:var(--paper);overflow:hidden;box-shadow:0 .25em .9em rgba(0,0,0,.28)}
.slide.dark{background:var(--dark);color:#fff}
.slide > *{position:absolute}

.hd{left:4%;top:6%;font-size:.62em;font-weight:700;text-transform:uppercase;letter-spacing:.02em;color:var(--ink)}
.hd em{font-style:normal;color:var(--gold)}
.hd.case{text-transform:none}
.ft{left:0;right:0;bottom:0;height:5%;border-top:1px solid var(--line);display:flex;justify-content:space-between;align-items:center;padding:0 3%;font-size:.26em;color:var(--grey)}
.ft b{color:var(--gold);font-weight:700}
.dark .ft{border-color:#3a3a40}
.p{font-size:.3em;line-height:1.3;color:var(--text);font-weight:500}
.p b{color:var(--ink);font-weight:700}
.p b.g{color:var(--gold)}
.dark .p{color:#c4c4c4}
.ph{background:var(--photo-site)}
.ph.sky{background:var(--photo-sky)}
.ph.warm{background:var(--photo-warm)}
.gbox{background:linear-gradient(90deg,var(--gold-d),var(--gold-l));color:#fff;padding:3%}
.gbox .p{color:#fff7e6}
.gbox .p b{color:#fff}
.gtitle{font-size:.38em;font-weight:700;color:var(--gold)}

.brand{left:6%;top:16%;width:38%;text-align:center;display:flex;flex-direction:column;align-items:center}
.brand i{width:1.6em;height:1.6em;border:.14em solid var(--gold);margin-bottom:.25em}
.brand b{font-size:.9em;font-weight:700;color:var(--gold);letter-spacing:.06em;text-transform:uppercase}
.t-title{left:6%;top:46%;width:38%;text-align:center;font-size:.82em;font-weight:700;color:var(--gold);line-height:1.2}
.t-sub{left:6%;top:66%;width:38%;text-align:center;font-size:.36em;color:#555;line-height:1.3}
.dark .t-sub{color:#ccc}
.t-dots{left:6%;top:77%;width:38%;display:flex;justify-content:center;gap:.35em}
.t-dots i{width:1em;height:1em;border-radius:50%;background:var(--ink)}
.dark .t-dots i{background:#fff}
.house{left:44%;top:0;width:56%;height:95%;clip-path:polygon(0 100%,0 50%,38% 12%,58% 32%,58% 20%,80% 0,100% 18%,100% 100%)}

.ag-panel{left:0;top:0;width:32%;height:100%;background:linear-gradient(180deg,#3a3a40,#1d1d22)}
.ag-word{left:3%;top:46%;font-size:.62em;font-weight:700;color:#fff;letter-spacing:.05em}
.ag-person{left:18%;top:0;width:26%;height:100%}
.ag-list{left:49%;top:12%;width:46%;list-style:none}
.ag-list li{position:relative;font-size:.42em;padding:.55em 0 .55em 1.8em;border-bottom:1px solid var(--line);color:#333}
.ag-list li::before{content:"";position:absolute;left:0;top:.65em;width:1em;height:1em;border-radius:50%;background:var(--gold)}

.stat{display:flex;align-items:center;justify-content:space-around}
.stat div{text-align:center;color:#fff}
.stat b{display:block;font-size:.7em;font-weight:700}
.stat span{font-size:.24em}

.card{background:#fff;box-shadow:0 .1em .4em rgba(0,0,0,.18);display:flex;flex-direction:column;align-items:center;text-align:center;padding:3% 2%}
.card .gtitle{margin:.4em 0 .2em;font-size:.3em}
.ico{width:1.3em;height:1.3em;border:.1em solid var(--gold);border-radius:.2em;display:flex;align-items:center;justify-content:center}
.ico svg,.hex svg{width:70%;height:70%;fill:none;stroke:var(--gold);stroke-width:2;stroke-linecap:round;stroke-linejoin:round}
.hex svg{stroke:#fff;width:45%;height:45%}

.member{background:var(--ink);display:flex;flex-direction:column;align-items:center;justify-content:flex-end;padding:0 6% 4%;text-align:center}
.member .face{width:40%;aspect-ratio:1;border-radius:50%;background:var(--photo-sky);margin-bottom:auto;margin-top:-18%;border:.15em solid #fff}
.member .p{color:#ccc;margin-bottom:.5em}
.member b{font-size:.3em;color:#fff;font-weight:700}

.plan{background:#fff;box-shadow:0 .1em .5em rgba(0,0,0,.2);display:flex;flex-direction:column;align-items:center;padding-top:2%}
.plan h4{font-size:.34em;font-weight:600;color:#333;margin:.4em 0}
.plan .price{width:100%;background:var(--ink);color:#fff;text-align:center;font-size:.55em;font-weight:600;padding:.3em 0}
.plan.feat .price{background:var(--gold)}
.plan ul{list-style:none;width:85%;margin-top:.6em}
.plan li{font-size:.22em;color:#777;padding:.25em 0;border-bottom:1px solid var(--line)}
.plan li::before{content:"✓ ";color:var(--gold)}
.plan .btn{margin-top:auto;margin-bottom:8%;width:50%;padding:.1em 0;background:#999;color:#fff;font-size:.2em;text-align:center}
.plan.feat .btn{background:var(--gold)}

.track{left:6%;top:56%;width:88%;height:1px;background:#bbb}
.node{width:1.6em;height:1.6em;border-radius:50%;border:.12em solid var(--ink);background:#fff;display:flex;align-items:center;justify-content:center;transform:translate(-50%,-50%)}
.node span{font-size:.3em;font-weight:700}

.bars{display:flex;align-items:flex-end;gap:3%;border-bottom:1px solid #bbb;border-left:1px solid #bbb;padding:0 3%}
.bars i{flex:1;background:linear-gradient(180deg,var(--gold-l),var(--gold-d))}
.ring{border-radius:50%;display:flex;align-items:center;justify-content:center}
.ring::after{content:"";position:absolute;inset:18%;border-radius:50%;background:#fff}
.ring b{position:relative;z-index:1;font-size:.42em;font-weight:600;color:#444}
.tbl{border-collapse:collapse;font-size:.22em;color:#555}
.tbl th{background:var(--gold);color:#fff;font-weight:600;padding:.3em}
.tbl td{border-bottom:1px solid var(--line);padding:.3em;text-align:center}
.tbl td:first-child{text-align:left}

.tile{background:#e3e3e3;display:flex;align-items:center;justify-content:center}
.tile i{width:30%;aspect-ratio:1;background:#bdbdbd}
.dotg{width:1.2em;height:1.2em;border-radius:50%;background:var(--gold)}
.vline{width:1px;background:var(--gold)}
.hex{clip-path:polygon(25% 4%,75% 4%,100% 50%,75% 96%,25% 96%,0 50%);display:flex;align-items:center;justify-content:center;text-align:center}
.hex span{font-size:.2em;color:#fff;font-weight:600;line-height:1.2}
.vlabel{font-size:.4em;font-weight:700;transform:rotate(-90deg);transform-origin:left top;white-space:nowrap;color:var(--ink)}
.vlabel em{font-style:normal;color:var(--gold)}
.stars{font-size:.26em;color:var(--gold);letter-spacing:.1em}

.iconset{left:4%;width:92%}
.setname{left:0;right:0;text-align:center;font-size:.26em;color:var(--gold);font-weight:600}

.quote{left:8%;top:40%;width:84%;text-align:center;font-size:.42em;line-height:1.3;color:#fff}
.thanks{left:0;right:0;top:52%;text-align:center;font-size:1.05em;font-weight:700;color:#fff}
</style>
</head>
<body>
<svg class="defs" aria-hidden="true">
  <symbol id="i-house" viewBox="0 0 24 24"><path d="M3 11 12 3l9 8M5 10v10h14V10M10 20v-6h4v6"/></symbol>
  <symbol id="i-clock" viewBox="0 0 24 24"><circle cx="12" cy="12" r="9"/><path d="M12 7v5l3 2"/></symbol>
  <symbol id="i-send" viewBox="0 0 24 24"><path d="M3 11 21 3l-8 18-2-8z"/></symbol>
  <symbol id="i-doc" viewBox="0 0 24 24"><path d="M6 3h9l4 4v14H6zM9 11h7M9 15h7"/></symbol>
  <symbol id="i-bank" viewBox="0 0 24 24"><path d="M3 9 12 4l9 5M5 10v8M10 10v8M14 10v8M19 10v8M3 20h18"/></symbol>
  <symbol id="i-tool" viewBox="0 0 24 24"><path d="M14 4a4 4 0 0 0 5 5l-9 9a2 2 0 0 1-3-3z"/></symbol>
  <symbol id="i-chart" viewBox="0 0 24 24"><path d="M4 20V4M4 20h16M8 16v-4M12 16V8M16 16v-6"/></symbol>
  <symbol id="i-people" viewBox="0 0 24 24"><circle cx="9" cy="8" r="3"/><circle cx="17" cy="9" r="2.5"/><path d="M3 20c0-4 3-6 6-6s6 2 6 6M15 14c3 0 6 2 6 5"/></symbol>
  <symbol id="i-power" viewBox="0 0 24 24"><path d="M12 3v8M7 6a7 7 0 1 0 10 0"/></symbol>
  <symbol id="i-pin" viewBox="0 0 24 24"><path d="M12 21s-7-7-7-12a7 7 0 0 1 14 0c0 5-7 12-7 12z"/><circle cx="12" cy="9" r="2.5"/></symbol>
  <symbol id="i-phone" viewBox="0 0 24 24"><path d="M5 3h4l2 5-3 2a11 11 0 0 0 6 6l2-3 5 2v4a2 2 0 0 1-2 2A17 17 0 0 1 3 5a2 2 0 0 1 2-2z"/></symbol>
  <symbol id="i-mail" viewBox="0 0 24 24"><path d="M3 6h18v12H3zM3 6l9 7 9-7"/></symbol>
  <pattern id="icongrid" width="32" height="8" patternUnits="userSpaceOnUse">
    <g fill="none" stroke="#c8902e" stroke-width=".7">
      <circle cx="4" cy="4" r="2.4"/><rect x="9.6" y="1.6" width="4.8" height="4.8" rx="1"/>
      <path d="M20 1.5 22.6 6.4H17.4z"/><path d="M28 1.6v4.8M25.6 4h4.8"/>
    </g>
  </pattern>
</svg>
<main class="canvas">

<div class="hero">
  <section class="slide">
    <h2 class="hd">Pricing <em>Tables</em></h2>
    <div class="plan" style="left:10%;top:22%;width:24%;height:66%"><h4>Comfort</h4><div class="price">$750</div><ul><li>Site cost review</li><li>Schedule check</li><li>Base plan audit</li></ul><div class="btn">Book Now</div></div>
    <div class="plan feat" style="left:38%;top:18%;width:24%;height:72%"><h4>Premium</h4><div class="price">$899</div><ul><li>Full cost plan</li><li>Team workshop</li><li>Tender support</li><li>Site visits</li></ul><div class="btn">Book Now</div></div>
    <div class="plan" style="left:66%;top:22%;width:24%;height:66%"><h4>Business</h4><div class="price">$850</div><ul><li>Cost tracking</li><li>Monthly report</li><li>Plan updates</li></ul><div class="btn">Book Now</div></div>
    <footer class="ft"><b>Nivel Crest</b><span>© 2023 Nivel Crest</span></footer>
  </section>

  <section class="slide">
    <div class="brand"><i></i><b>Nivel Crest</b></div>
    <h1 class="t-title">Presentation Title<br>Goes Here</h1>
    <p class="t-sub">Credential Subtitle<br>Presentation</p>
    <div class="t-dots"><i></i><i></i><i></i><i></i></div>
    <div class="ph house" role="img" aria-label="Building under construction with crane at sunset"></div>
    <footer class="ft"><span>© 2023 Nivel Crest</span><span></span></footer>
  </section>

  <section class="slide">
    <div class="ag-panel"></div>
    <div class="ph ag-person" role="img" aria-label="Construction engineer in a yellow hard hat"></div>
    <div class="ag-word">AGENDA</div>
    <ul class="ag-list"><li>Table of content</li><li>About Us</li><li>Tender Overview</li><li>Our Services</li><li>Our Team</li><li>Contact us</li></ul>
    <footer class="ft"><b>Nivel Crest</b><span>© 2023 Nivel Crest</span></footer>
  </section>

  <section class="slide">
    <h2 class="hd">3D <em>Infographics</em></h2>
    <p class="p" style="left:20%;top:17%;width:26%;text-align:right"><b class="g">Step 05</b><br>Final plan signed off with the owner and team</p>
    <p class="p" style="left:16%;top:31%;width:26%;text-align:right"><b class="g">Step 04</b><br>Cost targets fixed for every trade on site</p>
    <p class="p" style="left:12%;top:45%;width:26%;text-align:right"><b class="g">Step 03</b><br>Tender prepared and offers compared</p>
    <p class="p" style="left:8%;top:59%;width:26%;text-align:right"><b class="g">Step 02</b><br>Site and drawings reviewed in detail</p>
    <p class="p" style="left:4%;top:73%;width:26%;text-align:right"><b class="g">Step 01</b><br>Brief and budget collected from client</p>
    <svg style="left:48%;top:14%;width:48%;height:78%" viewBox="0 0 100 100" preserveAspectRatio="none" aria-hidden="true">
      <polygon points="0,100 0,82 16,78 16,96" fill="#b8801f"/>
      <polygon points="20,96 20,66 36,62 36,92" fill="#e0ad3a"/>
      <polygon points="40,92 40,48 56,44 56,88" fill="#3b3b40"/>
      <polygon points="60,88 60,34 76,30 76,84" fill="#8e8e92"/>
      <polygon points="80,84 80,26 88,26 84,4 96,0 100,26 100,80" fill="#c8902e"/>
    </svg>
    <footer class="ft"><b>Nivel Crest</b><span>© 2023 Nivel Crest</span></footer>
  </section>
</div>

<div class="deck">

  <section class="slide"><div class="brand"><i></i><b>Nivel Crest</b></div><h1 class="t-title">Presentation Title<br>Goes Here</h1><p class="t-sub">Credential Subtitle<br>Presentation</p><div class="t-dots"><i></i><i></i><i></i><i></i></div><div class="ph house" role="img" aria-label="Building site with crane"></div><footer class="ft"><span>© 2023 Nivel Crest</span><span></span></footer></section>
  <section class="slide dark"><div class="brand"><i></i><b>Nivel Crest</b></div><h1 class="t-title">Presentation Title<br>Goes Here</h1><p class="t-sub">Credential Subtitle<br>Presentation</p><div class="t-dots"><i></i><i></i><i></i><i></i></div><div class="ph house" role="img" aria-label="Building site with crane"></div><footer class="ft"><span>© 2023 Nivel Crest</span><span></span></footer></section>
  <section class="slide"><div class="ph sky" style="left:0;top:0;width:100%;height:95%;opacity:.35" role="img" aria-label="Faded construction team background"></div><div class="brand"><i></i><b>Nivel Crest</b></div><h1 class="t-title">Presentation Title<br>Goes Here</h1><p class="t-sub">Credential Subtitle<br>Presentation</p><div class="t-dots"><i></i><i></i><i></i><i></i></div><div class="ph warm house" role="img" aria-label="Engineers in hard hats reviewing plans"></div><footer class="ft"><span>© 2023 Nivel Crest</span><span></span></footer></section>
  <section class="slide dark"><div class="brand"><i></i><b>Nivel Crest</b></div><h1 class="t-title">Presentation Title<br>Goes Here</h1><p class="t-sub">Credential Subtitle<br>Presentation</p><div class="t-dots"><i></i><i></i><i></i><i></i></div><div class="ph warm house" role="img" aria-label="Engineers in hard hats reviewing plans"></div><footer class="ft"><span>© 2023 Nivel Crest</span><span></span></footer></section>
  <section class="slide"><div class="brand"><i></i><b>Nivel Crest</b></div><h1 class="t-title">Presentation Title<br>Goes Here</h1><p class="t-sub">Credential Subtitle<br>Presentation</p><div class="t-dots"><i></i><i></i><i></i><i></i></div><div class="ph sky house" role="img" aria-label="City skyline with cranes"></div><footer class="ft"><span>© 2023 Nivel Crest</span><span></span></footer></section>

  <section class="slide dark"><div class="brand"><i></i><b>Nivel Crest</b></div><h1 class="t-title">Presentation Title<br>Goes Here</h1><p class="t-sub">Credential Subtitle<br>Presentation</p><div class="t-dots"><i></i><i></i><i></i><i></i></div><div class="ph sky house" role="img" aria-label="High-rise under construction"></div><footer class="ft"><span>© 2023 Nivel Crest</span><span></span></footer></section>
  <section class="slide"><div class="ag-panel"></div><div class="ph ag-person" role="img" aria-label="Construction engineer in a yellow hard hat"></div><div class="ag-word">AGENDA</div><ul class="ag-list"><li>Table of content</li><li>About Us</li><li>Tender Overview</li><li>Our Services</li><li>Our Team</li><li>Contact us</li></ul><footer class="ft"><b>Nivel Crest</b><span>© 2023 Nivel Crest</span></footer></section>
  <section class="slide"><h2 class="hd">About <em>Us</em></h2><div class="gbox stat" style="left:4%;top:20%;width:60%;height:22%"><div><b>10+</b><span>Years of Work</span></div><div><b>240+</b><span>Projects Done</span></div></div><div class="ph" style="left:64%;top:14%;width:36%;height:34%" role="img" aria-label="Worker in orange vest on site"></div><p class="p" style="left:4%;top:54%;width:42%">We plan every build step so clients save cost and time on site. Our planners check drawings, quantities and offers, then set a clear budget that each partner can follow from the first survey to the final handover of the keys.</p><p class="p" style="left:52%;top:54%;width:42%">Our team reviews tenders and contracts to find savings before the first stone is laid. Clear reports keep the owner in control of money, risk and schedule during every single phase of the project.</p><footer class="ft"><b>Nivel Crest</b><span>© 2023 Nivel Crest</span></footer></section>
  <section class="slide"><h2 class="hd">Our <em>History</em></h2><p class="p" style="left:4%;top:18%;width:44%">Founded by engineers and planners, we grew from one small office into a team that guides builders through every phase of a project. Each year we add new tools for cost control and keep our advice simple and honest. Today we support private owners, developers and public clients across the region. We check designs early, compare offers line by line and track every change on site. Our clients value clear numbers, short reports and a partner who speaks plainly about risk, time and money from start to finish.</p><div class="gbox" style="left:68%;top:14%;width:28%;height:22%"><p class="p"><b>Since 2013</b><br>Planning for better builds.</p></div><div class="ph sky" style="left:54%;top:40%;width:38%;height:46%" role="img" aria-label="House model on desk"></div><footer class="ft"><b>Nivel Crest</b><span>© 2023 Nivel Crest</span></footer></section>
  <section class="slide"><h2 class="hd case">Why Are <em>We Here?</em></h2><div class="ph sky" style="left:4%;top:20%;width:38%;height:42%" role="img" aria-label="House model with coins"></div><div class="gbox" style="left:44%;top:28%;width:56%;height:30%"><p class="p">We help builders cut waste and keep every project on budget. Early planning finds the savings that later cost the most to fix on site.</p></div><p class="p" style="left:4%;top:68%;width:42%">Smart planning saves money long before construction starts. We set targets that every trade can meet on time.</p><p class="p" style="left:52%;top:68%;width:42%">We bring clarity to costs, timelines and contracts so owners can decide fast and with confidence.</p><footer class="ft"><b>Nivel Crest</b><span>© 2023 Nivel Crest</span></footer></section>

  <section class="slide"><h2 class="hd">Why You Should <em>Choose Us?</em></h2><p class="p" style="left:4%;top:18%;width:42%">Independent advice with a sharp eye on every cost line of your build. We compare options, check quantities and flag risks early in the design. Our reports stay short and clear.</p><p class="p" style="left:52%;top:18%;width:42%">Proven methods that shorten schedules and reduce change orders. We stay with you from the first sketch to handover and keep every partner aligned on budget and time.</p><div class="gbox" style="left:8%;top:62%;width:48%;height:22%"><p class="p"><b>Get Started</b><br>Book a first planning review with our team.</p></div><div class="ph warm" style="left:56%;top:56%;width:44%;height:38%" role="img" aria-label="Hands signing a contract beside a house model"></div><footer class="ft"><b>Nivel Crest</b><span>© 2023 Nivel Crest</span></footer></section>
  <section class="slide"><h2 class="hd case">Our Great <em>Vision</em></h2><div class="ph sky" style="left:4%;top:26%;width:30%;height:52%" role="img" aria-label="Desk with glasses and house model"></div><div class="gbox" style="left:34%;top:46%;width:60%;height:20%;display:flex;gap:8%"><p class="p"><b>Simple Text</b><br>Clear plans for all.</p><p class="p"><b>Simple Text</b><br>Fair costs for all.</p></div><p class="p" style="left:52%;top:20%;width:44%">A future where every build starts with a clear cost plan and a realistic schedule.</p><p class="p" style="left:40%;top:70%;width:54%">We make planning simple, shared and measurable so owners, designers and contractors work toward one goal.</p><footer class="ft"><b>Nivel Crest</b><span>© 2023 Nivel Crest</span></footer></section>
  <section class="slide"><h2 class="hd">Our <em>Services/Work</em></h2><div class="card" style="left:14%;top:22%;width:22%;height:66%"><div class="ph" style="position:static;width:100%;height:30%" role="img" aria-label="Site at dusk"></div><span class="gtitle">SERVICE ONE</span><p class="p">Cost planning for new builds with clear targets for each trade and phase.</p></div><div class="card" style="left:39%;top:22%;width:22%;height:66%"><div class="ph sky" style="position:static;width:100%;height:30%" role="img" aria-label="City towers"></div><span class="gtitle">SERVICE TWO</span><p class="p">Tender review and bid checks so every offer is fair and complete.</p></div><div class="card" style="left:64%;top:22%;width:22%;height:66%"><div class="ph warm" style="position:static;width:100%;height:30%" role="img" aria-label="Modern house"></div><span class="gtitle">SERVICE THREE</span><p class="p">Schedule and site control with short weekly reports for owners.</p></div><footer class="ft"><b>Nivel Crest</b><span>© 2023 Nivel Crest</span></footer></section>
  <section class="slide"><h2 class="hd">Our <em>Value</em></h2>
    <div class="ico" style="left:10%;top:25%"><svg><use href="#i-house"/></svg></div><p class="p" style="left:18%;top:24%;width:28%"><b class="g">Content here</b><br>Honest cost advice for every owner and builder.</p>
    <div class="ico" style="left:52%;top:25%"><svg><use href="#i-clock"/></svg></div><p class="p" style="left:60%;top:24%;width:28%"><b class="g">Content here</b><br>Clear timelines that trades can really meet.</p>
    <div class="ico" style="left:10%;top:47%"><svg><use href="#i-send"/></svg></div><p class="p" style="left:18%;top:46%;width:28%"><b class="g">Content here</b><br>Shared planning with short, open reports.</p>
    <div class="ico" style="left:52%;top:47%"><svg><use href="#i-doc"/></svg></div><p class="p" style="left:60%;top:46%;width:28%"><b class="g">Content here</b><br>Lean budgets checked line by line.</p>
    <div class="ico" style="left:10%;top:69%"><svg><use href="#i-tool"/></svg></div><p class="p" style="left:18%;top:68%;width:28%"><b class="g">Content here</b><br>Fair contracts for every partner.</p>
    <div class="ico" style="left:52%;top:69%"><svg><use href="#i-bank"/></svg></div><p class="p" style="left:60%;top:68%;width:28%"><b class="g">Content here</b><br>Site support until final handover.</p>
    <footer class="ft"><b>Nivel Crest</b><span>© 2023 Nivel Crest</span></footer></section>
  <section class="slide"><h2 class="hd">Our <em>Team</em></h2>
    <div class="member" style="left:14%;top:36%;width:22%;height:52%"><div class="face" role="img" aria-label="Team member portrait"></div><p class="p">Lead planner with fifteen years on large sites.</p><b>Mara Lindqvist</b></div>
    <div class="member" style="left:39%;top:36%;width:22%;height:52%"><div class="face" role="img" aria-label="Team member portrait"></div><p class="p">Cost engineer for tenders and contracts.</p><b>Theo Banner</b></div>
    <div class="member" style="left:64%;top:36%;width:22%;height:52%"><div class="face" role="img" aria-label="Team member portrait"></div><p class="p">Site manager for schedule and quality.</p><b>Jon Riedel</b></div>
    <footer class="ft"><b>Nivel Crest</b><span>© 2023 Nivel Crest</span></footer></section>

  <section class="slide"><h2 class="hd">Two Text <em>Columns</em></h2><div class="gbox" style="left:84%;top:4%;width:14%;height:14%"><p class="p">Image Holder</p></div><p class="p" style="left:4%;top:20%;width:44%">We review designs early and flag costly details. Our planners compare options, check quantities and set a budget every partner can follow through each stage of the build. Savings are tracked and reported monthly. We also check offers for missing items, compare unit prices with market values and advise on the best order of work. Each change on site is priced before it happens so the owner always knows the final cost. This keeps surprises small and decisions fast for the whole team.</p><p class="p" style="left:52%;top:20%;width:44%">From foundation to roof we keep a close eye on the plan. Each change is priced before it happens so the owner stays in control of money and time. Clear reports keep the whole team aligned. We meet the site team every week, update the schedule and share a short note with open points. When risks appear we propose options with cost and time, so the client can choose quickly. At handover we deliver a final report with all costs, savings and lessons learned.</p><footer class="ft"><b>Nivel Crest</b><span>© 2023 Nivel Crest</span></footer></section>
  <section class="slide"><h2 class="hd">Two Text <em>Columns</em></h2><p class="p" style="left:4%;top:20%;width:44%">Planning is where most savings are made. We set clear goals, check every offer and keep the schedule realistic for all trades on site. Our team works with architects and engineers to simplify details that add cost without adding value. Every decision is written down with its price and its effect on time.</p><p class="p" style="left:52%;top:20%;width:44%">Our reports give owners a simple view of cost, risk and progress so decisions are quick and well founded. We compare planned and real costs each month and explain every gap in plain words. This way the budget stays under control and the project stays on track.</p><div class="gbox" style="left:52%;top:72%;width:44%;height:16%"><p class="p"><b>Image Holder</b><br>Short caption for the picture.</p></div><footer class="ft"><b>Nivel Crest</b><span>© 2023 Nivel Crest</span></footer></section>
  <section class="slide"><h2 class="hd">Three Text <em>Columns</em></h2><div class="gbox" style="left:94%;top:0;width:6%;height:80%"></div><p class="p" style="left:4%;top:20%;width:27%">We study drawings and specs to spot extra cost early in the design. Options are compared with clear prices and the owner picks the best mix of quality, cost and time. Every choice is recorded for the team so nothing gets lost later on site.</p><p class="p" style="left:34%;top:20%;width:27%">Tenders are checked line by line so prices stay fair and clear. We look for missing items, odd unit rates and risky terms, then help you negotiate. The result is a contract that matches the plan and protects the budget.</p><p class="p" style="left:64%;top:20%;width:27%">On site we track progress and keep every trade on schedule. Weekly meetings, short notes and a live cost sheet show where the project stands. When something changes, we price it first and let the owner decide.</p><footer class="ft"><b>Nivel Crest</b><span>© 2023 Nivel Crest</span></footer></section>
  <section class="slide"><h2 class="hd">Text And <em>Picture Slide</em></h2><p class="p" style="left:4%;top:22%;width:44%">Good pictures tell the story of a project. Pair a short text with a strong site photo to show progress and results. Describe the challenge, the plan we built and the savings we reached. Keep it brief so the picture can speak. Add the project size, budget and time frame to give the client a clear sense of scale and success.</p><div class="ph" style="left:54%;top:16%;width:42%;height:66%" role="img" aria-label="Crane over a building site at sunset"></div><div class="gbox" style="left:42%;top:72%;width:22%;height:14%"><p class="p">Image Holder</p></div><footer class="ft"><b>Nivel Crest</b><span>© 2023 Nivel Crest</span></footer></section>
  <section class="slide"><div class="vlabel" style="left:3%;top:78%">Image <em>Gallery</em></div><div class="ph warm" style="left:8%;top:6%;width:30%;height:40%" role="img" aria-label="Workers on site"></div><div class="gbox" style="left:40%;top:6%;width:32%;height:40%;display:flex;flex-direction:column;justify-content:center;text-align:center"><div class="ico" style="border-color:#fff;margin:0 auto .4em"><svg style="stroke:#fff"><use href="#i-house"/></svg></div><p class="p"><b>Service Name</b><br>Short note on the work shown here.</p></div><div class="ph sky" style="left:74%;top:6%;width:22%;height:80%" role="img" aria-label="Tall building"></div><div class="ph" style="left:8%;top:50%;width:30%;height:36%" role="img" aria-label="Builders at work"></div><div class="ph warm" style="left:40%;top:50%;width:32%;height:36%" role="img" aria-label="House models"></div><footer class="ft"><b>Nivel Crest</b><span>© 2023 Nivel Crest</span></footer></section>

  <section class="slide"><div class="vlabel" style="left:3%;top:78%">Image <em>Gallery</em></div><div class="ph sky" style="left:8%;top:6%;width:30%;height:40%" role="img" aria-label="Building facade"></div><div class="ph warm" style="left:40%;top:6%;width:36%;height:40%" role="img" aria-label="Plans on a table"></div><div class="gbox" style="left:78%;top:6%;width:18%;height:40%"></div><div class="gbox" style="left:8%;top:50%;width:30%;height:36%;display:flex;flex-direction:column;justify-content:center"><div class="ico" style="border-color:#fff;margin-bottom:.4em"><svg style="stroke:#fff"><use href="#i-house"/></svg></div><p class="p"><b>Service Name</b><br>Short note on the work shown here.</p></div><div class="ph" style="left:40%;top:50%;width:24%;height:36%" role="img" aria-label="Engineer on site"></div><div class="ph warm" style="left:66%;top:50%;width:30%;height:36%" role="img" aria-label="Hands with house model"></div><footer class="ft"><b>Nivel Crest</b><span>© 2023 Nivel Crest</span></footer></section>
  <section class="slide"><h2 class="hd">Image <em>Gallery</em></h2><div class="ph sky" style="left:4%;top:20%;width:32%;height:44%" role="img" aria-label="House model with keys"></div><div class="ph" style="left:38%;top:20%;width:22%;height:40%" role="img" aria-label="Engineers in vests"></div><p class="p" style="left:64%;top:20%;width:32%">Show finished work and active sites side by side. A gallery helps clients see the quality of our planning in real results. Add a short line for each picture with place, year and scope of work.</p><div class="gbox" style="left:30%;top:64%;width:48%;height:18%"><p class="p">Short caption that explains the pictures and the savings reached.</p></div><footer class="ft"><b>Nivel Crest</b><span>© 2023 Nivel Crest</span></footer></section>
  <section class="slide"><h2 class="hd">Pricing <em>Tables</em></h2><div class="plan" style="left:10%;top:22%;width:24%;height:66%"><h4>Comfort</h4><div class="price">$750</div><ul><li>Cost review</li><li>Plan check</li><li>Base audit</li></ul><div class="btn">Book Now</div></div><div class="plan feat" style="left:38%;top:18%;width:24%;height:72%"><h4>Premium</h4><div class="price">$899</div><ul><li>Full plan</li><li>Workshop</li><li>Tender help</li><li>Site visits</li></ul><div class="btn">Book Now</div></div><div class="plan" style="left:66%;top:22%;width:24%;height:66%"><h4>Business</h4><div class="price">$850</div><ul><li>Tracking</li><li>Reports</li><li>Updates</li></ul><div class="btn">Book Now</div></div><footer class="ft"><b>Nivel Crest</b><span>© 2023 Nivel Crest</span></footer></section>
  <section class="slide"><h2 class="hd">Process <em>Slide</em></h2><div class="track"></div>
    <div class="node" style="left:14%;top:56%"><span>01</span></div><div class="node" style="left:28%;top:56%"><span>02</span></div><div class="node" style="left:42%;top:56%"><span>03</span></div><div class="node" style="left:56%;top:56%"><span>04</span></div><div class="node" style="left:70%;top:56%"><span>05</span></div><div class="node" style="left:84%;top:56%"><span>06</span></div>
    <div class="ico" style="left:26%;top:18%;border:none"><svg><use href="#i-doc"/></svg></div><p class="p" style="left:18%;top:27%;width:20%;text-align:center"><b>Content</b><br>Brief and goals set</p>
    <div class="ico" style="left:54%;top:18%;border:none"><svg><use href="#i-chart"/></svg></div><p class="p" style="left:46%;top:27%;width:20%;text-align:center"><b>Content</b><br>Tender prepared</p>
    <div class="ico" style="left:82%;top:18%;border:none"><svg><use href="#i-house"/></svg></div><p class="p" style="left:74%;top:27%;width:20%;text-align:center"><b>Content</b><br>Handover done</p>
    <div class="ico" style="left:12%;top:66%;border:none"><svg><use href="#i-pin"/></svg></div><p class="p" style="left:4%;top:75%;width:20%;text-align:center"><b>Content</b><br>Site survey</p>
    <div class="ico" style="left:40%;top:66%;border:none"><svg><use href="#i-bank"/></svg></div><p class="p" style="left:32%;top:75%;width:20%;text-align:center"><b>Content</b><br>Budget fixed</p>
    <div class="ico" style="left:68%;top:66%;border:none"><svg><use href="#i-tool"/></svg></div><p class="p" style="left:60%;top:75%;width:20%;text-align:center"><b>Content</b><br>Build tracked</p>
    <footer class="ft"><b>Nivel Crest</b><span>© 2023 Nivel Crest</span></footer></section>
  <section class="slide"><h2 class="hd">Process <em>Flowchart</em></h2>
    <svg style="left:4%;top:14%;width:92%;height:78%" viewBox="0 0 100 60" aria-hidden="true">
      <g fill="none" stroke="#999" stroke-width=".4"><path d="M14 30 H30 M38 30 H46 M50 12 H70 M50 48 H70 M58 30 H64 M72 30 H80"/></g>
      <circle cx="10" cy="30" r="5" fill="#fff" stroke="#c8902e" stroke-width="1.2"/>
      <circle cx="34" cy="30" r="4" fill="#fff" stroke="#c8902e" stroke-width="1.2"/>
      <rect x="46" y="6" width="8" height="48" rx="4" fill="#1f1f23"/>
      <circle cx="50" cy="14" r="2.4" fill="#fff"/><circle cx="50" cy="30" r="2.4" fill="#fff"/><circle cx="50" cy="46" r="2.4" fill="#fff"/>
      <rect x="62" y="26" width="8" height="8" transform="rotate(45 66 30)" fill="#fff" stroke="#c8902e" stroke-width="1"/>
      <rect x="76" y="9" width="20" height="6" rx="3" fill="#ddd"/><rect x="76" y="45" width="20" height="6" rx="3" fill="#ddd"/>
      <circle cx="79" cy="12" r="2.2" fill="#fff" stroke="#999" stroke-width=".4"/><circle cx="79" cy="48" r="2.2" fill="#fff" stroke="#999" stroke-width=".4"/>
      <g font-family="Montserrat,sans-serif" font-size="2" fill="#555" text-anchor="middle"><text x="10" y="40">Project Title</text><text x="34" y="38">Process</text><text x="54" y="5">Option 1</text><text x="86" y="7">Result</text><text x="67" y="40">Yes</text><text x="86" y="55">Option 2</text></g>
    </svg>
    <footer class="ft"><b>Nivel Crest</b><span>© 2023 Nivel Crest</span></footer></section>

  <section class="slide"><h2 class="hd">Data Driven <em>Chart</em></h2><div class="bars" style="left:8%;top:18%;width:84%;height:62%"><i style="height:4%"></i><i style="height:6%"></i><i style="height:9%"></i><i style="height:12%"></i><i style="height:17%"></i><i style="height:24%"></i><i style="height:32%"></i><i style="height:44%"></i><i style="height:58%"></i><i style="height:76%"></i><i style="height:92%"></i></div>
    <svg style="left:8%;top:18%;width:84%;height:62%" viewBox="0 0 100 100" preserveAspectRatio="none" aria-hidden="true"><polyline points="4,96 13,94 22,90 31,86 40,80 49,72 58,62 67,50 76,36 85,22 94,8" fill="none" stroke="#c8902e" stroke-width="1"/></svg>
    <p class="p" style="left:8%;top:83%;width:84%;text-align:center">2013 2014 2015 2016 2017 2018 2019 2020 2021 2022 2023 · Column One · Column Two</p>
    <footer class="ft"><b>Nivel Crest</b><span>© 2023 Nivel Crest</span></footer></section>
  <section class="slide"><h2 class="hd">Data Driven <em>Chart Slide</em></h2><p class="p" style="left:4%;top:22%;width:30%">Track cost savings across years with a clear bar view. Each bar shows the money saved against the first budget. Use the notes to explain the main drivers and the plan for next year.</p><div style="left:38%;top:20%;width:46%;height:64%;border:.35em solid #2a2a2e;border-radius:.4em;background:#fff"></div><div class="bars" style="left:44%;top:30%;width:34%;height:46%"><i style="height:40%"></i><i style="height:70%"></i><i style="height:55%"></i><i style="height:85%"></i><i style="height:60%"></i><i style="height:95%"></i></div><div class="gbox" style="left:86%;top:44%;width:10%;height:10%;border-radius:1em"></div><footer class="ft"><b>Nivel Crest</b><span>© 2023 Nivel Crest</span></footer></section>
  <section class="slide"><h2 class="hd">Data Driven <em>Pie Charts</em></h2><p class="p" style="left:8%;top:18%;width:84%;text-align:center">Show the share of savings per project phase in simple rings. Each ring compares the planned cost with the final cost and the value we added for the owner.</p>
    <div class="ring" style="left:14%;top:36%;width:18%;aspect-ratio:1;background:conic-gradient(var(--gold) 0 75%,#e9e9e9 0)"><b>75%</b></div>
    <div class="ring" style="left:41%;top:36%;width:18%;aspect-ratio:1;background:conic-gradient(var(--gold) 0 85%,#e9e9e9 0)"><b>85%</b></div>
    <div class="ring" style="left:68%;top:36%;width:18%;aspect-ratio:1;background:conic-gradient(var(--gold) 0 55%,#e9e9e9 0)"><b>55%</b></div>
    <p class="p" style="left:10%;top:74%;width:26%;text-align:center">Design phase savings on site</p><p class="p" style="left:37%;top:74%;width:26%;text-align:center">Tender phase savings on offers</p><p class="p" style="left:64%;top:74%;width:26%;text-align:center">Build phase savings on changes</p>
    <footer class="ft"><b>Nivel Crest</b><span>© 2023 Nivel Crest</span></footer></section>
  <section class="slide"><h2 class="hd">Data Driven <em>Line Chart</em></h2><div class="gbox" style="left:6%;top:18%;width:50%;height:7%;padding:0"><p class="p" style="text-align:center">Chart Title</p></div>
    <svg style="left:6%;top:28%;width:50%;height:56%" viewBox="0 0 100 60" preserveAspectRatio="none" aria-hidden="true"><path d="M0 60 H100 M0 0 V60" stroke="#ccc" stroke-width=".6"/><polyline points="4,38 20,20 36,44 52,30 68,36 84,14 96,10" fill="none" stroke="#c8902e" stroke-width="1"/><polyline points="4,30 20,40 36,28 52,46 68,24 84,30 96,18" fill="none" stroke="#444" stroke-width="1"/></svg>
    <p class="p" style="left:6%;top:86%;width:50%;text-align:center">Series 1 · Series 2</p>
    <p class="p" style="left:62%;top:28%;width:34%">Compare planned and real costs month by month. The gold line shows the plan, the dark line the actual spend. Where the lines part, add a short note on the cause and the action taken to bring the project back on budget.</p>
    <footer class="ft"><b>Nivel Crest</b><span>© 2023 Nivel Crest</span></footer></section>
  <section class="slide"><h2 class="hd">Pricing <em>Table</em></h2>
    <table class="tbl" style="left:8%;top:28%;width:84%"><tr><th></th><th>A</th><th>B</th><th>C</th><th>D</th></tr><tr><td>Content A</td><td>100</td><td>200</td><td>400</td><td>800</td></tr><tr><td>Content B</td><td>$67,000</td><td>$56,000</td><td>$76,000</td><td>$80,000</td></tr><tr><td>Content C</td><td>4600</td><td>60000</td><td>$6,000</td><td>$20,000</td></tr><tr><td>Content D</td><td>3400</td><td>$400</td><td>$600</td><td>$1,200</td></tr><tr><td>Content E</td><td>$55</td><td>$800</td><td>$1,000</td><td>$3,400</td></tr></table>
    <footer class="ft"><b>Nivel Crest</b><span>© 2023 Nivel Crest</span></footer></section>

  <section class="slide"><h2 class="hd">Our <em>Client</em></h2>
    <div style="left:10%;top:22%;width:44%;height:64%;display:grid;grid-template-columns:repeat(3,1fr);gap:8%"><span class="tile"><i></i></span><span class="tile"><i></i></span><span class="tile"><i></i></span><span class="tile"><i></i></span><span class="tile"><i></i></span><span class="tile"><i></i></span><span class="tile"><i></i></span><span class="tile"><i></i></span><span class="tile"><i></i></span><span class="tile"><i></i></span><span class="tile"><i></i></span><span class="tile"><i></i></span></div>
    <div class="dotg" style="left:60%;top:28%"></div><p class="p" style="left:68%;top:26%;width:28%">Developers and private owners who want a clear budget.</p>
    <div class="dotg" style="left:60%;top:48%"></div><p class="p" style="left:68%;top:46%;width:28%">General contractors who need fair and complete tenders.</p>
    <div class="dotg" style="left:60%;top:68%"></div><p class="p" style="left:68%;top:66%;width:28%">Public building offices with strict cost rules.</p>
    <footer class="ft"><b>Nivel Crest</b><span>© 2023 Nivel Crest</span></footer></section>
  <section class="slide"><h2 class="hd">Project Title <em>Goes Here</em></h2><p class="p" style="left:4%;top:17%;width:92%">A short project summary with location, size, budget and the savings we achieved for the owner. Describe the main challenge, the planning steps we took and the final result delivered on time. Keep it to three or four lines for a clean layout.</p><div class="ph sky" style="left:6%;top:40%;width:28%;height:46%" role="img" aria-label="Stairs and steel structure"></div><div class="ph warm" style="left:36%;top:40%;width:28%;height:46%" role="img" aria-label="Finished cabins"></div><div class="ph sky" style="left:66%;top:40%;width:28%;height:46%" role="img" aria-label="Steel hall"></div><footer class="ft"><b>Nivel Crest</b><span>© 2023 Nivel Crest</span></footer></section>
  <section class="slide"><div class="gbox" style="left:0;top:0;width:4%;height:100%"></div><div class="ph warm" style="left:10%;top:10%;width:38%;height:36%" role="img" aria-label="Modular building exterior"></div><p class="gtitle" style="left:56%;top:12%">PROJECT TITLE GOES<br>HERE 1</p><p class="p" style="left:56%;top:26%;width:40%">Site offices finished in eight weeks with a budget saving of twelve percent for the owner.</p><p class="gtitle" style="left:10%;top:52%">PROJECT TITLE GOES<br>HERE 2</p><p class="p" style="left:10%;top:66%;width:40%">Modular units delivered under budget thanks to early tender checks and clear planning.</p><div class="ph warm" style="left:56%;top:50%;width:38%;height:36%" role="img" aria-label="Modular units on site"></div><footer class="ft"><b>Nivel Crest</b><span>© 2023 Nivel Crest</span></footer></section>
  <section class="slide"><h2 class="hd">Our <em>Timeline</em></h2><p class="p" style="left:8%;top:18%;width:84%;text-align:center">Key milestones from our first project to today. Each step shows how our team and services grew with the needs of our clients.</p><div class="vline" style="left:50%;top:38%;height:57%"></div><div class="gbox" style="left:46%;top:42%;width:8%;height:5%;padding:0"><p class="p" style="text-align:center">2013</p></div><p class="p" style="left:18%;top:54%;width:28%;text-align:right"><b>Your Subtitle Here</b><br>First office opened with a small team of planners.</p><div class="ph" style="left:54%;top:54%;width:28%;height:22%" role="img" aria-label="Building site"></div><div class="ico" style="left:42%;top:78%"><svg><use href="#i-house"/></svg></div><p class="p" style="left:56%;top:79%;width:30%">March · Team grows</p><footer class="ft"><b>Nivel Crest</b><span>© 2023 Nivel Crest</span></footer></section>
  <section class="slide"><div class="vline" style="left:50%;top:0;height:95%"></div><div class="ph warm" style="left:8%;top:8%;width:36%;height:26%" role="img" aria-label="Workers on site"></div><p class="p" style="left:56%;top:16%;width:36%"><b>Your Subtitle Here</b><br>Team grew to twenty planners and engineers.</p><div class="ico" style="left:10%;top:38%"><svg><use href="#i-chart"/></svg></div><p class="p" style="left:18%;top:38%;width:26%">April · New tools</p><p class="p" style="left:8%;top:52%;width:36%;text-align:right"><b>Your Subtitle Here</b><br>New region opened for public clients.</p><div class="ph sky" style="left:56%;top:44%;width:38%;height:28%" role="img" aria-label="Engineer pointing at towers"></div><div class="ico" style="left:56%;top:76%"><svg><use href="#i-pin"/></svg></div><p class="p" style="left:64%;top:76%;width:30%">May · New office</p><footer class="ft"><b>Nivel Crest</b><span>© 2023 Nivel Crest</span></footer></section>

  <section class="slide"><div class="vline" style="left:50%;top:0;height:56%"></div><div class="ph warm" style="left:8%;top:10%;width:36%;height:26%" role="img" aria-label="Tools on plans"></div><p class="p" style="left:56%;top:20%;width:36%"><b>Your Subtitle Here</b><br>Digital planning tools added for live cost tracking.</p><div class="ico" style="left:10%;top:40%"><svg><use href="#i-doc"/></svg></div><p class="p" style="left:18%;top:40%;width:26%">June · Reports</p><div class="gbox" style="left:46%;top:54%;width:8%;height:5%;padding:0"><p class="p" style="text-align:center">2023</p></div><p class="gtitle" style="left:0;right:0;top:64%;text-align:center;color:var(--ink)">End Timeline</p><p class="p" style="left:10%;top:73%;width:80%;text-align:center">Today we guide over forty builds every year and help owners save on each one through clear and early planning.</p><footer class="ft"><b>Nivel Crest</b><span>© 2023 Nivel Crest</span></footer></section>
  <section class="slide dark"><div class="gbox" style="left:0;top:0;width:100%;height:16%"></div><div style="left:66%;top:0;width:30%;height:30%;background:#fff;display:flex;align-items:center;justify-content:center;gap:.3em"><i style="width:.9em;height:.9em;border:.1em solid var(--gold)"></i><b style="font-size:.4em;color:var(--gold);font-weight:700">NIVEL CREST</b></div><p class="quote">“Lorem ipsum dolor sit amet, consectetuer adipiscing elit. Maecenas porttitor congue massa. Fusce posuere, magna sed pulvinar ultricies.”</p><footer class="ft"><b>Nivel Crest</b><span>© 2023 Nivel Crest</span></footer></section>
  <section class="slide"><h2 class="hd">Client <em>Testimonial</em></h2>
    <div class="card" style="left:10%;top:28%;width:24%;height:58%"><div class="ph" style="position:static;width:36%;aspect-ratio:1;border-radius:50%" role="img" aria-label="Client portrait"></div><span class="stars">★★★★★</span><p class="p">They saved us weeks and kept our budget safe.</p><b style="font-size:.26em;margin-top:.4em">Lena Ward</b></div>
    <div class="card" style="left:38%;top:20%;width:24%;height:70%;background:var(--dark)"><div class="ph sky" style="position:static;width:36%;aspect-ratio:1;border-radius:50%" role="img" aria-label="Client portrait"></div><span class="stars">★★★★★</span><p class="p" style="color:#ccc">Clear and honest advice from start to handover.</p><b style="font-size:.26em;margin-top:.4em;color:var(--gold)">Omar Velez</b></div>
    <div class="card" style="left:66%;top:28%;width:24%;height:58%"><div class="ph" style="position:static;width:36%;aspect-ratio:1;border-radius:50%" role="img" aria-label="Client portrait"></div><span class="stars">★★★★★</span><p class="p">Budget kept to the euro on a large build.</p><b style="font-size:.26em;margin-top:.4em">Ruth Haley</b></div>
    <footer class="ft"><b>Nivel Crest</b><span>© 2023 Nivel Crest</span></footer></section>
  <section class="slide"><div class="ph sky" style="left:6%;top:8%;width:36%;height:82%" role="img" aria-label="Businessman in suit portrait"></div><div class="gbox" style="left:42%;top:10%;width:1.5%;height:14%;padding:0"></div><p class="gtitle" style="left:46%;top:12%;color:var(--ink)">Testimonial</p><p class="gtitle" style="left:46%;top:20%;font-size:.7em">“</p><p class="p" style="left:46%;top:34%;width:48%">Working with this team cut our build cost and kept every trade on time. Their reports were short, clear and always honest about risk. We will plan our next project together.</p><div class="gbox" style="left:34%;top:66%;width:44%;height:18%;display:flex;align-items:center;gap:4%"><div class="ico" style="border-color:#fff;flex:none"><svg style="stroke:#fff"><use href="#i-house"/></svg></div><p class="p">Owner of a residential project with forty homes.</p></div><footer class="ft"><b>Nivel Crest</b><span>© 2023 Nivel Crest</span></footer></section>
  <section class="slide"><h2 class="hd">3D <em>Infographics</em></h2>
    <p class="p" style="left:24%;top:17%;width:26%;text-align:right"><b class="g">Step 05</b><br>Sign off with owner</p><p class="p" style="left:20%;top:31%;width:26%;text-align:right"><b class="g">Step 04</b><br>Fix costs per trade</p><p class="p" style="left:16%;top:45%;width:26%;text-align:right"><b class="g">Step 03</b><br>Tender and compare</p><p class="p" style="left:12%;top:59%;width:26%;text-align:right"><b class="g">Step 02</b><br>Review site and plans</p><p class="p" style="left:8%;top:73%;width:26%;text-align:right"><b class="g">Step 01</b><br>Collect the brief</p>
    <svg style="left:52%;top:10%;width:44%;height:82%" viewBox="0 0 100 100" preserveAspectRatio="none" aria-hidden="true"><polygon points="0,100 0,82 16,78 16,96" fill="#b8801f"/><polygon points="20,96 20,66 36,62 36,92" fill="#e0ad3a"/><polygon points="40,92 40,48 56,44 56,88" fill="#3b3b40"/><polygon points="60,88 60,34 76,30 76,84" fill="#8e8e92"/><polygon points="80,84 80,26 88,26 84,4 96,0 100,26 100,80" fill="#c8902e"/></svg>
    <footer class="ft"><b>Nivel Crest</b><span>© 2023 Nivel Crest</span></footer></section>

  <section class="slide"><h2 class="hd">Our Customer <em>Segments</em></h2>
    <div class="hex" style="left:10%;top:20%;width:15%;height:24%;background:var(--brown)"><span>YOUR CONTENT HERE</span></div>
    <div class="hex" style="left:23%;top:32%;width:15%;height:24%;background:var(--gold-d)"><span>YOUR CONTENT HERE</span></div>
    <div class="hex" style="left:36%;top:20%;width:15%;height:24%;background:var(--brown)"><span>YOUR CONTENT HERE</span></div>
    <div class="hex" style="left:49%;top:32%;width:15%;height:24%;background:var(--gold)"><span>YOUR CONTENT HERE</span></div>
    <div class="hex" style="left:62%;top:20%;width:15%;height:24%;background:var(--gold-l)"><span>YOUR CONTENT HERE</span></div>
    <p class="p" style="left:8%;top:62%;width:84%;text-align:center">Owners, developers, contractors and public clients each get a plan that fits their goals and budget. We adapt our reports, meetings and tools to the size of the project and to the way each client likes to work, so every decision is easy and well prepared.</p>
    <footer class="ft"><b>Nivel Crest</b><span>© 2023 Nivel Crest</span></footer></section>
  <section class="slide"><h2 class="hd">Our Range <em>Of Services</em></h2>
    <div class="hex" style="left:10%;top:22%;width:11%;height:18%;background:var(--brown)"><svg><use href="#i-tool"/></svg></div><div class="hex" style="left:22%;top:22%;width:11%;height:18%;background:var(--brown)"><svg><use href="#i-chart"/></svg></div><div class="hex" style="left:34%;top:22%;width:11%;height:18%;background:var(--brown)"><svg><use href="#i-people"/></svg></div>
    <div class="hex" style="left:16%;top:42%;width:11%;height:18%;background:var(--brown)"><svg><use href="#i-doc"/></svg></div><div class="hex" style="left:28%;top:42%;width:11%;height:18%;background:var(--gold-d)"><svg><use href="#i-house"/></svg></div>
    <div class="hex" style="left:22%;top:62%;width:11%;height:18%;background:var(--brown)"><svg><use href="#i-clock"/></svg></div>
    <div class="hex" style="left:72%;top:36%;width:11%;height:18%;background:var(--brown)"><svg><use href="#i-people"/></svg></div><div class="hex" style="left:66%;top:56%;width:11%;height:18%;background:var(--brown)"><svg><use href="#i-tool"/></svg></div><div class="hex" style="left:78%;top:56%;width:11%;height:18%;background:var(--brown)"><svg><use href="#i-power"/></svg></div>
    <p class="p" style="left:44%;top:46%;width:18%;transform:rotate(-60deg)">Lorem ipsum dolor</p><p class="p" style="left:56%;top:40%;width:18%;transform:rotate(-60deg)">Lorem ipsum dolor</p>
    <footer class="ft"><b>Nivel Crest</b><span>© 2023 Nivel Crest</span></footer></section>
  <section class="slide"><h2 class="hd">3D <em>Infographics</em></h2><p class="p" style="left:4%;top:18%;width:44%">Pair a product view with short facts and three key numbers for the client. Explain how live data from the site reaches the owner in seconds. Progress, cost and time are always at hand, on any device, so decisions stay quick and clear for everyone involved in the build.</p><div class="ph sky" style="left:54%;top:16%;width:32%;height:62%;border-radius:1.2em" role="img" aria-label="Smartwatch showing a building site"></div>
    <div class="ring" style="left:8%;top:66%;width:8%;aspect-ratio:1;background:conic-gradient(var(--gold) 0 45%,#e9e9e9 0)"><b style="font-size:.2em">45</b></div><div class="ring" style="left:22%;top:66%;width:8%;aspect-ratio:1;background:conic-gradient(var(--gold) 0 75%,#e9e9e9 0)"><b style="font-size:.2em">75</b></div><div class="ring" style="left:36%;top:66%;width:8%;aspect-ratio:1;background:conic-gradient(var(--gold) 0 60%,#e9e9e9 0)"><b style="font-size:.2em">60</b></div>
    <footer class="ft"><b>Nivel Crest</b><span>© 2023 Nivel Crest</span></footer></section>
  <section class="slide"><h2 class="hd">Phone <em>Mockup</em></h2><p class="p" style="left:6%;top:20%;width:40%">Show your planning app or project report on a phone screen. Keep the text short and the view clean. Mention the main features: live cost sheet, photo log of the site, weekly schedule and a simple list of open points for the owner and the team. Every update is shared with all partners at once.</p><div class="ph" style="left:50%;top:28%;width:44%;height:52%;border-radius:.8em;transform:rotate(-18deg)" role="img" aria-label="Phone showing construction workers"></div><footer class="ft"><b>Nivel Crest</b><span>© 2023 Nivel Crest</span></footer></section>
  <section class="slide"><h2 class="hd">Screen <em>Mockup</em></h2><div class="ph warm" style="left:10%;top:22%;width:44%;height:56%" role="img" aria-label="Laptop showing a house project"></div><p class="p" style="left:62%;top:24%;width:34%">Present site reports and plans on a laptop view for your client meetings. Show the cost sheet, the schedule and the latest site photos side by side. A clear screen view helps owners follow the project and make fast, well founded decisions.</p><footer class="ft"><b>Nivel Crest</b><span>© 2023 Nivel Crest</span></footer></section>

  <section class="slide"><div class="ph sky" style="left:0;top:0;width:46%;height:95%" role="img" aria-label="Hand touching a digital world map"></div><h2 class="hd" style="left:50%">Get In <em>Touch</em></h2>
    <div class="ico" style="left:52%;top:27%;border:none"><svg><use href="#i-pin"/></svg></div><p class="p" style="left:59%;top:27%;width:36%"><b class="g">Office</b><br>12 Harbour Lane</p>
    <div class="ico" style="left:52%;top:45%;border:none"><svg><use href="#i-pin"/></svg></div><p class="p" style="left:59%;top:45%;width:36%"><b class="g">UAE Offices</b><br>Tower 4, Level 9</p>
    <div class="ico" style="left:52%;top:62%;border:none"><svg><use href="#i-phone"/></svg></div><p class="p" style="left:59%;top:64%;width:36%">0123 4567</p>
    <div class="ico" style="left:52%;top:73%;border:none"><svg><use href="#i-mail"/></svg></div><p class="p" style="left:59%;top:75%;width:36%">hello@nivelcrest.com</p>
    <footer class="ft"><b>Nivel Crest</b><span>© 2023 Nivel Crest</span></footer></section>
  <section class="slide dark"><p class="setname" style="top:8%">General</p><svg class="iconset" style="top:16%;height:44%" aria-hidden="true"><rect width="100%" height="100%" fill="url(#icongrid)"/></svg><p class="setname" style="top:62%">Electronics</p><svg class="iconset" style="top:70%;height:22%" aria-hidden="true"><rect width="100%" height="100%" fill="url(#icongrid)"/></svg></section>
  <section class="slide dark"><p class="setname" style="top:5%">E-commerce</p><svg class="iconset" style="top:11%;height:20%" aria-hidden="true"><rect width="100%" height="100%" fill="url(#icongrid)"/></svg><p class="setname" style="top:33%">Web</p><svg class="iconset" style="top:39%;height:18%" aria-hidden="true"><rect width="100%" height="100%" fill="url(#icongrid)"/></svg><p class="setname" style="top:59%">Location</p><svg class="iconset" style="top:65%;height:8%" aria-hidden="true"><rect width="100%" height="100%" fill="url(#icongrid)"/></svg><p class="setname" style="top:75%">Arrows</p><svg class="iconset" style="top:81%;height:14%" aria-hidden="true"><rect width="100%" height="100%" fill="url(#icongrid)"/></svg></section>
  <section class="slide dark"><p class="setname" style="top:8%">Weather</p><svg class="iconset" style="top:16%;height:18%" aria-hidden="true"><rect width="100%" height="100%" fill="url(#icongrid)"/></svg><p class="setname" style="top:36%">Miscellaneous</p><svg class="iconset" style="top:44%;height:48%" aria-hidden="true"><rect width="100%" height="100%" fill="url(#icongrid)"/></svg></section>
  <section class="slide dark"><div class="brand" style="left:30%;top:26%;width:40%"><i></i><b>Nivel Crest</b></div><p class="thanks">Thank you</p><div class="gbox" style="left:0;top:84%;width:44%;height:6%;padding:0"></div></section>

</div>
</main>
</body>
</html>
```